Modern, high quality Surfing Earplug company

New Zealand based and inspired, Surfing Eaplugs for USA Online Banner Advert campaign. We require a simple - wow factor banner advert that communicates the surfing and beach lifestyle, rather than a total product focus.

A design that can incorporate all three people from these pics is desirable. The VORN logo should always be in capitals, in the Anurati font, and in black or reverse white. The tagline is "Protect Your Ears, Surf for a Lifetime"
Nothing too fancy please. It must be optimized for the web
Updates

Hello all,thanks for so many great efforts! Please note the following banner sizes will be needed for Desktop, Tablet and Mobile phone 300 x 600 320 x 50 300 x 250 728 x 90 970 x 90 Thanks Dale

Target Market(s)

25 to 50 year old male and female surfers and swimmers in the USA

Industry/Entity Type

It Company

Font styles to use
Sans Serif

Colors
3276b5
33a6d7
ffc623
fbed22
ec1f27

Requirements
Must have
• VORN logo: either in black or white reverse.
• Tagline: "Protect your Ears - Surf for a Lifetime' exactly how it's written here
• Be optimized for the web
Nice to have
• All the people on the brief included. I'm not too concerned if not possible, but must be at least 2 males and 1 female
• Simple, clean and strong!
• A sunrise or sunset, nice blue waves on the beach for effect
Should not have
• Overcrowded design elements

```html
<!DOCTYPE html>
<html lang="en">
<head>
<meta charset="utf-8">
<title>VORN Surf Earplugs – Banner Set</title>
<link rel="stylesheet" href="https://fonts.googleapis.com/css2?family=Lato:ital,wght@0,700;1,400&family=Roboto+Condensed:wght@500&display=swap">
<style>
  :root {
    --board: #2a2a2a;
    --ink: #262626;
    --sky-light: #eef2f6;
    --sky-mid: #cfdbe6;
    --shade: #3c4341;
    --shade-deep: #1d1f22;
    --btn-top: #ffd21f;
    --btn-bottom: #f5a300;
    --btn-edge: #c98400;
    --arrow-disc: #f4f4f4;
  }
  * { box-sizing: border-box; margin: 0; padding: 0; }
  html, body { width: 1200px; height: 1200px; overflow: hidden; }
  body { background: var(--board); position: relative; font-family: "Lato", sans-serif; color: var(--ink); }

  .banner { position: absolute; overflow: hidden; }
  .banner-photo { position: absolute; inset: 0; }
  .brand { position: absolute; font-family: "Lato", sans-serif; font-weight: 700; color: var(--ink); letter-spacing: 0.08em; line-height: 1; }
  .headline { position: absolute; font-weight: 700; line-height: 1; white-space: nowrap; }
  .tagline { position: absolute; font-style: italic; font-weight: 400; line-height: 1; white-space: nowrap; }

  .order-btn {
    position: absolute; display: flex; align-items: center; justify-content: center; gap: 8px;
    background: linear-gradient(var(--btn-top), var(--btn-bottom));
    border: 1px solid var(--btn-edge); border-radius: 4px;
    font-family: "Roboto Condensed", sans-serif; font-weight: 500; color: #111;
    box-shadow: 0 2px 3px rgba(0,0,0,.35);
  }
  .order-btn svg { flex: none; }

  /* 300 x 600 */
  .skyscraper { left: 104px; top: 86px; width: 200px; height: 749px; }
  .skyscraper .banner-photo { background: linear-gradient(180deg, var(--sky-light) 0%, var(--sky-mid) 38%, #6f5e4b 55%, var(--shade) 75%, #5d7067 100%); }
  .skyscraper .brand { top: 28px; width: 100%; text-align: center; font-size: 50px; }
  .skyscraper .headline.l1 { top: 106px; width: 100%; text-align: center; font-size: 37px; }
  .skyscraper .headline.l2 { top: 143px; width: 100%; text-align: center; font-size: 30px; }
  .skyscraper .tagline { top: 176px; width: 100%; text-align: center; font-size: 19px; }
  .skyscraper .order-btn { left: 9px; top: 685px; width: 182px; height: 45px; font-size: 23px; }

  /* 300 x 250 */
  .rect-small { left: 312px; top: 165px; width: 375px; height: 312px; }
  .rect-small .banner-photo { background: linear-gradient(160deg, var(--sky-light) 0%, var(--sky-mid) 40%, #8a6e52 62%, var(--shade) 100%); }
  .rect-small .headline { top: 14px; left: 25px; font-size: 31px; }
  .rect-small .tagline { top: 50px; right: 26px; font-size: 20px; }
  .rect-small .brand { top: 110px; right: 30px; font-size: 40px; }
  .rect-small .order-btn { left: 199px; top: 260px; width: 164px; height: 40px; font-size: 21px; }

  /* 336 x 280 */
  .rect-large { left: 312px; top: 486px; width: 420px; height: 349px; }
  .rect-large .banner-photo { background: linear-gradient(160deg, var(--sky-light) 0%, var(--sky-mid) 40%, #8a6e52 62%, var(--shade) 100%); }
  .rect-large .headline { top: 14px; left: 28px; font-size: 35px; }
  .rect-large .tagline { top: 54px; right: 28px; font-size: 22px; }
  .rect-large .brand { top: 122px; right: 32px; font-size: 44px; }
  .rect-large .order-btn { left: 224px; top: 291px; width: 181px; height: 45px; font-size: 23px; }

  /* 728 x 90 */
  .leader-small { left: 104px; top: 850px; width: 585px; height: 72px; }
  .leader-small .banner-photo { background: linear-gradient(90deg, var(--sky-light) 0%, var(--sky-light) 17%, #8a6a4e 26%, var(--sky-mid) 40%, var(--sky-light) 60%, #7d8b84 82%, var(--shade-deep) 100%); }
  .leader-small .brand { top: 18px; left: 12px; font-size: 34px; }
  .leader-small .headline { top: 16px; left: 255px; font-size: 19px; }
  .leader-small .tagline { top: 38px; left: 275px; font-size: 19px; }
  .leader-small .order-btn { left: 462px; top: 20px; width: 112px; height: 28px; font-size: 14px; gap: 5px; }

  /* 970 x 90 */
  .leader-large { left: 104px; top: 935px; width: 910px; height: 111px; }
  .leader-large .banner-photo { background: linear-gradient(90deg, var(--sky-light) 0%, var(--sky-light) 14%, #8a6a4e 24%, #d7b69b 36%, var(--sky-light) 48%, var(--sky-light) 72%, #7d8b84 82%, var(--shade-deep) 100%); }
  .leader-large .brand { top: 32px; left: 14px; font-size: 48px; }
  .leader-large .headline { top: 26px; left: 396px; font-size: 29px; }
  .leader-large .tagline { top: 61px; left: 410px; font-size: 30px; }
  .leader-large .order-btn { left: 720px; top: 33px; width: 176px; height: 44px; font-size: 23px; }
</style>
</head>
<body>

  <section class="banner skyscraper">
    <div class="banner-photo" role="img" aria-label="Photo of a female surfer in a wetsuit holding a surfboard against a bright sky"></div>
    <div class="brand">VORN</div>
    <div class="headline l1">PROTECT</div>
    <div class="headline l2">YOUR EARS</div>
    <div class="tagline">Surf for a Lifetime</div>
    <div class="order-btn">Order Now!
      <svg width="24" height="24" viewBox="0 0 24 24"><circle cx="12" cy="12" r="11" fill="var(--arrow-disc)"/><path d="M10 7l5 5-5 5" fill="none" stroke="#111" stroke-width="2.6"/></svg>
    </div>
  </section>

  <section class="banner rect-small">
    <div class="banner-photo" role="img" aria-label="Photo of a female surfer wearing earplugs, holding a white surfboard"></div>
    <div class="headline">PROTECT YOUR EARS</div>
    <div class="tagline">Surf for a Lifetime</div>
    <div class="brand">VORN</div>
    <div class="order-btn">Order Now!
      <svg width="22" height="22" viewBox="0 0 24 24"><circle cx="12" cy="12" r="11" fill="var(--arrow-disc)"/><path d="M10 7l5 5-5 5" fill="none" stroke="#111" stroke-width="2.6"/></svg>
    </div>
  </section>

  <section class="banner rect-large">
    <div class="banner-photo" role="img" aria-label="Photo of a female surfer wearing earplugs, holding a white surfboard"></div>
    <div class="headline">PROTECT YOUR EARS</div>
    <div class="tagline">Surf for a Lifetime</div>
    <div class="brand">VORN</div>
    <div class="order-btn">Order Now!
      <svg width="24" height="24" viewBox="0 0 24 24"><circle cx="12" cy="12" r="11" fill="var(--arrow-disc)"/><path d="M10 7l5 5-5 5" fill="none" stroke="#111" stroke-width="2.6"/></svg>
    </div>
  </section>

  <section class="banner leader-small">
    <div class="banner-photo" role="img" aria-label="Photo strip of a female surfer in profile and a surfboard"></div>
    <div class="brand">VORN</div>
    <div class="headline">PROTECT YOUR EARS</div>
    <div class="tagline">Surf for a Lifetime</div>
    <div class="order-btn">Order Now!
      <svg width="16" height="16" viewBox="0 0 24 24"><circle cx="12" cy="12" r="11" fill="var(--arrow-disc)"/><path d="M10 7l5 5-5 5" fill="none" stroke="#111" stroke-width="2.8"/></svg>
    </div>
  </section>

  <section class="banner leader-large">
    <div class="banner-photo" role="img" aria-label="Photo strip of a female surfer in profile and a surfboard"></div>
    <div class="brand">VORN</div>
    <div class="headline">PROTECT YOUR EARS</div>
    <div class="tagline">Surf for a Lifetime</div>
    <div class="order-btn">Order Now!
      <svg width="24" height="24" viewBox="0 0 24 24"><circle cx="12" cy="12" r="11" fill="var(--arrow-disc)"/><path d="M10 7l5 5-5 5" fill="none" stroke="#111" stroke-width="2.6"/></svg>
    </div>
  </section>

</body>
</html>
```